Company web site

Looking for a full responsive(mobile friendly) wordpress implementation

Some material is in the website -- brelvanto.wordpress.com

But looking for a template more consistent with the logo design, and more future looking.

Target Market(s)

Enterprise Clients

Industry/Entity Type

It Company

Font styles to use
Sans Serif

Colors
33a6d7
0255a3
0455a3
cfdeed
85abd2
3176b5

Requirements
Must have
• about, contact information, partner page, success stories, customer testimonials. links to social presence.
• pricing information

```html
<!DOCTYPE html>
<html lang="en">
<head>
<meta charset="utf-8">
<title>Brelvanto — Cloud &amp; IT Services</title>
<link rel="stylesheet" href="https://fonts.googleapis.com/css2?family=Roboto:wght@300;400;500;700&display=swap">
<style>
:root{
  --blue-dark:#0255a3;
  --blue-mid:#3176b5;
  --blue-light:#33a6d7;
  --blue-soft:#85abd2;
  --blue-pale:#cfdeed;
  --ink:#333b44;
  --muted:#7a8591;
  --line:#e3e7eb;
  --panel:#f3f5f7;
  --white:#ffffff;
}
*{box-sizing:border-box;margin:0;padding:0}
html,body{width:1200px;height:2592px;overflow:hidden}
body{font-family:"Roboto",Arial,sans-serif;color:var(--ink);background:var(--white);font-size:13px;line-height:1.6}
.page{width:1200px;height:2592px;position:relative}

/* header */
.site-header{height:112px;display:flex;align-items:center;justify-content:space-between;padding:0 60px}
.brand{display:flex;align-items:center;gap:12px}
.brand-dot{width:34px;height:34px;border-radius:50%;background:var(--blue-light)}
.brand-name{font-size:30px;font-weight:700;color:var(--blue-dark);letter-spacing:.5px}
.main-nav{display:flex;gap:4px}
.main-nav a{font-size:12px;font-weight:500;color:var(--ink);text-decoration:none;padding:10px 16px;text-transform:uppercase;letter-spacing:.4px}
.main-nav a.is-active{background:var(--blue-dark);color:var(--white)}

/* hero */
.hero{height:480px;position:relative;background:linear-gradient(100deg,#0b2440 0%,#123a63 45%,#2d6ea6 75%,#1b4a78 100%);color:var(--white)}
.hero-copy{position:absolute;left:68px;top:140px;width:420px}
.hero-title{font-size:42px;font-weight:700;letter-spacing:1px;margin-bottom:14px}
.hero-text{font-size:14px;color:#dce8f4;line-height:1.7;margin-bottom:26px}
.btn{display:inline-block;font-size:12px;font-weight:700;letter-spacing:.6px;padding:11px 24px;text-transform:uppercase;color:var(--white);text-decoration:none}
.btn-dark{background:#0c2745;border:1px solid #5d84ad}
.btn-blue{background:var(--blue-dark)}
.hero-dots{position:absolute;left:68px;bottom:28px;display:flex;gap:8px}
.hero-dots span{width:10px;height:10px;border-radius:50%;border:2px solid var(--white)}
.hero-dots span.on{background:var(--white)}

/* section headings */
.section-title{font-size:38px;font-weight:300;color:var(--blue-light);text-align:center}
.section-sub{font-size:13px;color:var(--muted);text-align:center;margin-top:4px}

/* welcome */
.welcome{height:388px;padding-top:44px}
.features{display:grid;grid-template-columns:repeat(3,300px);justify-content:center;gap:56px;margin-top:34px;text-align:center}
.feature-icon{width:96px;height:96px;margin:0 auto 14px}
.feature-title{font-size:17px;font-weight:500;color:var(--blue-dark);margin-bottom:8px}
.feature-text{font-size:12px;color:var(--muted);line-height:1.6}
.link-more{display:inline-block;margin-top:8px;font-size:11px;font-weight:700;color:var(--blue-dark);text-decoration:none}

/* success */
.success{height:440px;background:var(--panel);display:flex;align-items:center;padding:0 100px;gap:70px}
.success-copy{width:440px}
.success-copy .section-title{text-align:left;margin-bottom:20px}
.success-copy p{font-size:13px;color:var(--muted);margin-bottom:26px;line-height:1.75}
.success-visual{width:480px;height:330px;border-radius:6px;background:linear-gradient(180deg,#e8ecf0 0%,#c9d2da 100%)}

/* services */
.services{height:500px;background:linear-gradient(180deg,#2c93d6 0%,#2a86c9 100%);padding-top:40px;color:var(--white)}
.services .section-title,.services .section-sub{color:var(--white)}
.services .section-sub{color:#d6e9f7}
.service-grid{display:grid;grid-template-columns:repeat(3,300px);justify-content:center;column-gap:70px;row-gap:50px;margin-top:50px}
.service{display:flex;gap:18px}
.service svg{flex:none;width:44px;height:44px}
.service h3{font-size:13px;font-weight:700;letter-spacing:.6px;margin-bottom:6px}
.service p{font-size:12px;color:#e2f0fa;line-height:1.6}

/* news & testimonials */
.news-testimonials{height:304px;display:flex;gap:60px;padding:26px 100px 0}
.news,.testimonials{width:470px}
.block-title{font-size:32px;font-weight:300;color:var(--blue-light);margin-bottom:16px}
.news-date{display:inline-block;background:var(--blue-dark);color:var(--white);font-size:11px;font-weight:700;padding:7px 14px;margin-bottom:14px}
.news p{font-size:12px;color:var(--muted);line-height:1.7}
.news a{color:var(--blue-dark);font-weight:700;text-decoration:none}
.testimonial{display:flex;gap:26px;align-items:flex-start}
.client-photo{flex:none;width:96px;height:96px;border-radius:50%;background:linear-gradient(160deg,#d8c2ad,#8b6a55);border:4px solid var(--blue-pale)}
.quote{position:relative;font-size:12px;color:var(--muted);font-style:italic;line-height:1.7;padding:0 18px}
.quote::before,.quote::after{position:absolute;font-size:36px;color:var(--blue-dark);font-style:normal;line-height:1}
.quote::before{content:"\201C";left:-6px;top:-6px}
.quote::after{content:"\201D";right:-4px;bottom:-22px}
.client-name{margin:16px 0 0 18px;font-size:12px;color:var(--blue-dark);font-weight:700}
.client-role{margin-left:18px;font-size:11px;color:var(--muted)}

/* footer */
.site-footer{height:306px;background:#eef1f4;display:flex;padding:36px 80px 0;gap:50px}
.footer-brand{width:210px;display:flex;align-items:flex-start;padding-top:30px}
.footer-brand .brand-name{font-size:28px}
.footer-col h4{font-size:20px;font-weight:400;color:var(--ink);margin-bottom:14px}
.contact-col{width:220px}
.contact-list{list-style:none}
.contact-list li{display:flex;gap:10px;align-items:flex-start;font-size:12px;color:var(--muted);margin-bottom:7px}
.contact-list svg{flex:none;width:14px;height:14px;margin-top:2px}
.news-col{width:240px}
.news-col p{font-size:12px;color:var(--muted);margin-bottom:12px}
.field{height:32px;border:1px solid #cdd4db;background:var(--white);font-size:11px;color:#9aa4ae;padding:7px 10px;margin-bottom:10px}
.btn-small{font-size:11px;padding:7px 16px}
.follow-col{width:200px}
.follow-col p{font-size:12px;color:var(--muted);margin-bottom:14px}
.social{display:flex;gap:8px}
.social span{width:28px;height:28px;border-radius:50%;border:1px solid #9aa4ae}
.copyright{height:62px;background:var(--blue-dark);color:#cfe0f0;font-size:12px;display:flex;align-items:center;justify-content:center}
</style>
</head>
<body>
<div class="page">

<header class="site-header">
  <div class="brand"><span class="brand-dot"></span><span class="brand-name">Brelvanto</span></div>
  <nav class="main-nav">
    <a class="is-active" href="#">Home</a>
    <a href="#">About</a>
    <a href="#">Partners</a>
    <a href="#">Pricing</a>
    <a href="#">Success Stories</a>
    <a href="#">Testimonials</a>
    <a href="#">Contact Us</a>
  </nav>
</header>

<section class="hero" role="img" aria-label="Businessman holding a tablet with glowing cloud network icons above it">
  <div class="hero-copy">
    <h1 class="hero-title">BRELVANTO</h1>
    <p class="hero-text">Brelvanto is company which provides specialized offerings in IoT domain. Based in the heart of the Silicon Valley, California, we are leaders of connected technology.</p>
    <a class="btn btn-dark" href="#">Read More</a>
  </div>
  <div class="hero-dots"><span class="on"></span><span></span><span></span></div>
</section>

<section class="welcome">
  <h2 class="section-title">Welcome to Brelvanto</h2>
  <p class="section-sub">Brelvanto can quick and deliver the features your customers need, based on our versatile architecture.</p>
  <div class="features">
    <article class="feature">
      <svg class="feature-icon" viewBox="0 0 96 96" aria-hidden="true">
        <circle cx="48" cy="48" r="46" fill="none" stroke="#c8d3de" stroke-width="2"/>
        <rect x="26" y="30" width="44" height="28" rx="2" fill="none" stroke="#0255a3" stroke-width="3"/>
        <path d="M20 64h56" stroke="#0255a3" stroke-width="4" stroke-linecap="round"/>
        <path d="M38 44l7 7 13-13" fill="none" stroke="#33a6d7" stroke-width="3" stroke-linecap="round"/>
      </svg>
      <h3 class="feature-title">Brelvanto Device</h3>
      <p class="feature-text">Start a smart connected device with secure onboarding, remote updates and live insight for every unit you deploy.</p>
      <a class="link-more" href="#">READ MORE</a>
    </article>
    <article class="feature">
      <svg class="feature-icon" viewBox="0 0 96 96" aria-hidden="true">
        <circle cx="48" cy="48" r="46" fill="none" stroke="#c8d3de" stroke-width="2"/>
        <rect x="36" y="24" width="24" height="16" fill="none" stroke="#0255a3" stroke-width="3"/>
        <rect x="20" y="58" width="20" height="14" fill="none" stroke="#0255a3" stroke-width="3"/>
        <rect x="56" y="58" width="20" height="14" fill="none" stroke="#0255a3" stroke-width="3"/>
        <path d="M48 40v9M30 58v-9h36v9" fill="none" stroke="#33a6d7" stroke-width="3"/>
      </svg>
      <h3 class="feature-title">Network Operation</h3>
      <p class="feature-text">Start a round-the-clock network operation centre that watches uptime, traffic and alerts across all your sites.</p>
      <a class="link-more" href="#">READ MORE</a>
    </article>
    <article class="feature">
      <svg class="feature-icon" viewBox="0 0 96 96" aria-hidden="true">
        <circle cx="48" cy="48" r="46" fill="none" stroke="#c8d3de" stroke-width="2"/>
        <path d="M30 62a12 12 0 0 1 2-24 16 16 0 0 1 30-4 12 12 0 0 1 4 28z" fill="none" stroke="#0255a3" stroke-width="3"/>
        <path d="M40 52h16M48 44v16" stroke="#33a6d7" stroke-width="3" stroke-linecap="round"/>
      </svg>
      <h3 class="feature-title">Cloud Services</h3>
      <p class="feature-text">Start a scalable cloud platform for storage, analytics and apps, managed by our team and tuned for enterprise load.</p>
      <a class="link-more" href="#">READ MORE</a>
    </article>
  </div>
</section>

<section class="success">
  <div class="success-copy">
    <h2 class="section-title">Success Stories</h2>
    <p>Founded in 2010 by industry veterans, Brelvanto is geared to provide integrated solutions for the IoT industry. With a off-shore development center in Eastern Europe, Brelvanto is positioned to provide innovative development capabilities to our customers. From a handful of early clients to a growing list of enterprise partners, Brelvanto helps teams launch connected products faster and with less risk.</p>
    <a class="btn btn-blue" href="#">Read More</a>
  </div>
  <div class="success-visual" role="img" aria-label="Desktop monitor showing a server and network architecture diagram"></div>
</section>

<section class="services">
  <h2 class="section-title">Our Services</h2>
  <p class="section-sub">Brelvanto can quick and deliver the features your customers need, based on our versatile architecture.</p>
  <div class="service-grid">
    <div class="service">
      <svg viewBox="0 0 44 44" aria-hidden="true"><circle cx="22" cy="22" r="8" fill="none" stroke="#fff" stroke-width="3"/><path d="M22 6v6M22 32v6M6 22h6M32 22h6M11 11l4 4M29 29l4 4M33 11l-4 4M15 29l-4 4" stroke="#fff" stroke-width="3" stroke-linecap="round"/></svg>
      <div><h3>MANUFACTURE</h3><p>Brelvanto builds hardware for connected products, from prototype to volume runs, tested in-house.</p></div>
    </div>
    <div class="service">
      <svg viewBox="0 0 44 44" aria-hidden="true"><path d="M8 34h28" stroke="#fff" stroke-width="3"/><rect x="10" y="22" width="6" height="12" fill="#fff"/><rect x="19" y="14" width="6" height="20" fill="#fff"/><rect x="28" y="8" width="6" height="26" fill="#fff"/></svg>
      <div><h3>SELL</h3><p>Brelvanto helps you bring devices to market with channel setup, pricing and partner sales support.</p></div>
    </div>
    <div class="service">
      <svg viewBox="0 0 44 44" aria-hidden="true"><path d="M8 18h8l14-8v24l-14-8H8z" fill="#fff"/><path d="M34 16a8 8 0 0 1 0 12" fill="none" stroke="#fff" stroke-width="3"/></svg>
      <div><h3>PROVIDER</h3><p>Brelvanto acts as your service provider, hosting platforms and APIs with a clear uptime promise.</p></div>
    </div>
    <div class="service">
      <svg viewBox="0 0 44 44" aria-hidden="true"><path d="M10 24a12 12 0 0 1 24 0" fill="none" stroke="#fff" stroke-width="3"/><rect x="6" y="24" width="7" height="10" rx="2" fill="#fff"/><rect x="31" y="24" width="7" height="10" rx="2" fill="#fff"/></svg>
      <div><h3>SUPPORT</h3><p>Brelvanto gives round-the-clock help desk and field support for every device and cloud service.</p></div>
    </div>
    <div class="service">
      <svg viewBox="0 0 44 44" aria-hidden="true"><rect x="6" y="10" width="32" height="22" rx="2" fill="none" stroke="#fff" stroke-width="3"/><path d="M12 26l7-7 5 4 8-8" fill="none" stroke="#fff" stroke-width="3"/></svg>
      <div><h3>MONETIZE</h3><p>Brelvanto turns device data into revenue with billing, subscriptions and usage-based plans.</p></div>
    </div>
    <div class="service">
      <svg viewBox="0 0 44 44" aria-hidden="true"><rect x="8" y="10" width="28" height="26" rx="2" fill="none" stroke="#fff" stroke-width="3"/><path d="M8 18h28M15 6v8M29 6v8" stroke="#fff" stroke-width="3"/><path d="M15 27l5 4 9-9" fill="none" stroke="#fff" stroke-width="3"/></svg>
      <div><h3>MAINTAIN</h3><p>Brelvanto keeps systems healthy with scheduled updates, patches and proactive health checks.</p></div>
    </div>
  </div>
</section>

<section class="news-testimonials">
  <div class="news">
    <h2 class="block-title">Latest News</h2>
    <span class="news-date">26 JUNE 2017</span>
    <p>Founded in 2010 by industry veterans, Brelvanto is geared to provide integrated solutions for the IoT industry. With a off-shore development center in Eastern Europe, Brelvanto is positioned to provide innovative development capabilities to our customers that is geographically spread across the entire country and beyond. <a href="#">MORE</a></p>
  </div>
  <div class="testimonials">
    <h2 class="block-title">Our Testimonials</h2>
    <div class="testimonial">
      <div class="client-photo" role="img" aria-label="Portrait photo of a client"></div>
      <div>
        <p class="quote">Brelvanto gave our team a stable cloud platform and a clear plan for our devices. Their support staff answer fast, know the product well and help us grow without worry. We would gladly work with them again.</p>
        <p class="client-name">Name, Dara Quill</p>
        <p class="client-role">Posted 26 June 2017</p>
      </div>
    </div>
  </div>
</section>

<footer class="site-footer">
  <div class="footer-brand"><div class="brand"><span class="brand-dot"></span><span class="brand-name">Brelvanto</span></div></div>
  <div class="footer-col contact-col">
    <h4>Contact Us</h4>
    <ul class="contact-list">
      <li><svg viewBox="0 0 14 14" aria-hidden="true"><path d="M3 1l2 3-1.5 1.5a8 8 0 0 0 5 5L10 9l3 2-1.5 2.5C6 13 1 8 .5 2.5z" fill="#0255a3"/></svg>+1 (408) 555-0147 (Office)</li>
      <li><svg viewBox="0 0 14 14" aria-hidden="true"><path d="M3 1l2 3-1.5 1.5a8 8 0 0 0 5 5L10 9l3 2-1.5 2.5C6 13 1 8 .5 2.5z" fill="#0255a3"/></svg>+1 (408) 555-0163 (Fax)</li>
      <li><svg viewBox="0 0 14 14" aria-hidden="true"><rect x="1" y="3" width="12" height="8" fill="none" stroke="#0255a3" stroke-width="1.5"/><path d="M1 3l6 5 6-5" fill="none" stroke="#0255a3" stroke-width="1.5"/></svg>info@brelvanto.com</li>
      <li><svg viewBox="0 0 14 14" aria-hidden="true"><path d="M7 13s-4.5-5-4.5-8a4.5 4.5 0 0 1 9 0c0 3-4.5 8-4.5 8z" fill="#0255a3"/><circle cx="7" cy="5" r="1.6" fill="#fff"/></svg>2140 Orchard Lane<br>Santa Clara, CA 95054</li>
    </ul>
  </div>
  <div class="footer-col news-col">
    <h4>Newsletter Signup</h4>
    <p>Register your email below to get the latest news and updates.</p>
    <div class="field">Email Address</div>
    <a class="btn btn-blue btn-small" href="#">Submit</a>
  </div>
  <div class="footer-col follow-col">
    <h4>Follow Us</h4>
    <p>Join our social pages for news, events and product updates from our team.</p>
    <div class="social"><span></span><span></span><span></span><span></span><span></span></div>
  </div>
</footer>

<div class="copyright">© Copyright 2017 | Brelvanto All Rights Reserved</div>

</div>
</body>
</html>
```